Clean business card with logo provided

I want a card that will stand out among the masses. I need the color and image to show professionalism and yet have a family appeal showing that I only deal with win/win scenarios. The back of the card will be used to take notes about the individual so I can use that in my database entry. I like modern design but need professionalism in it also. It needs to fit my "clean, safe, and affordable housing" motto. I need to be able to write on the file and update the card details for my employees.

Target Market(s)

Investors looking to make investment income through real estate

Industry/Entity Type

Real Estate

Contact Information for Business Card

Brent Kovalich
blank address, city, st, zip code
480-555-3174
brentkovalich@ridgeworthrentals.example
www.ridgeworthrentals.example

Font styles to use
Sans Serif

Requirements
Must have
• I would like the back of the card to have lines for info. example
• Met/Visited: Date:
• Interets:
Nice to have
• I want the cards color to match the logo background color. Font with details to be san serif and black. I want the card rectangular with square corners. Standard business card size. I would like to see cards designed with both images to see which i prefer more.

```html
<!DOCTYPE html>
<html lang="en">
<head>
<meta charset="utf-8">
<title>Ridgeworth Rentals LLC – Business Card</title>
<link rel="stylesheet" href="https://fonts.googleapis.com/css2?family=Cinzel:wght@500&family=Open+Sans:wght@400;600&display=swap">
<style>
  :root {
    --teal: #0a98b1;
    --teal-deep: #087f95;
    --black: #050505;
    --white: #ffffff;
    --paper: #ececec;
    --swoosh: #e9e9ee;
    --ink: #111111;
    --rule: #1a1a1a;
    --backdrop: #d7d7d7;
  }
  * { box-sizing: border-box; margin: 0; padding: 0; }
  html, body {
    width: 1105px; height: 1200px; overflow: hidden;
    background: var(--backdrop);
    font-family: "Open Sans", Arial, sans-serif;
  }
  .canvas { position: relative; width: 1105px; height: 1200px; }

  .card { position: absolute; left: 180px; width: 746px; height: 427px; overflow: hidden; }
  .card--front { top: 119px; background: var(--black); }
  .card--back { top: 637px; background: var(--paper); }

  .front-wave { position: absolute; inset: 0; width: 100%; height: 100%; }

  .wordmark {
    position: absolute; display: flex; flex-direction: column; align-items: center;
  }
  .wordmark__row { display: flex; align-items: center; gap: 12px; }
  .wordmark__name {
    font-family: "Cinzel", Georgia, serif; font-weight: 500;
    font-size: 30px; letter-spacing: 2px; line-height: 1; white-space: nowrap;
  }
  .wordmark__dot { width: 22px; height: 22px; border-radius: 50%; }
  .wordmark__motto { font-size: 11px; margin-top: 8px; letter-spacing: 0.2px; }

  .card--front .wordmark { top: 62px; right: 40px; }
  .card--front .wordmark__name { color: var(--teal); }
  .card--front .wordmark__dot { background: var(--white); }
  .card--front .wordmark__motto { color: var(--teal); }

  .holder-name {
    position: absolute; top: 158px; right: 60px;
    font-family: "Cinzel", Georgia, serif; font-weight: 500;
    font-size: 25px; color: var(--teal); letter-spacing: 0.5px;
  }

  .address {
    position: absolute; left: 35px; top: 244px;
    color: var(--white); font-size: 19.5px; line-height: 29px;
  }
  .contact-list {
    position: absolute; left: 35px; top: 312px; list-style: none;
    color: var(--white); font-size: 19.5px; line-height: 29px;
  }
  .contact-list li { display: flex; align-items: center; gap: 10px; }
  .contact-list svg { width: 18px; height: 18px; flex: none; fill: var(--white); }

  .back-band { position: absolute; left: 0; top: 0; width: 100%; height: 209px; background: var(--teal); }
  .card--back .wordmark { top: 62px; left: 0; right: 0; }
  .card--back .wordmark__name { color: var(--black); font-size: 34px; }
  .card--back .wordmark__dot { background: var(--black); }
  .card--back .wordmark__motto { color: var(--white); font-size: 12px; }

  .note-field {
    position: absolute; display: flex; align-items: flex-end;
    color: var(--teal); font-size: 18.5px; font-weight: 400; letter-spacing: 0.2px;
  }
  .note-field__line { border-bottom: 1.5px solid var(--rule); height: 1px; margin-left: 8px; margin-bottom: 5px; }
  .field-met { left: 56px; top: 262px; }
  .field-date { left: 451px; top: 262px; }
  .field-interests { left: 56px; top: 315px; }
  .blank-line { position: absolute; left: 62px; top: 391px; width: 620px; border-bottom: 1.5px solid var(--rule); }
</style>
</head>
<body>
<div class="canvas">

  <section class="card card--front" aria-label="Card front">
    <svg class="front-wave" viewBox="0 0 746 427" preserveAspectRatio="none" aria-hidden="true">
      <path d="M0,158 C120,130 270,150 390,225 C500,295 610,345 746,300 L746,427 L0,427 Z" fill="var(--swoosh)"/>
      <path d="M0,160 C120,135 260,160 380,235 C490,305 600,370 746,338 L746,427 L0,427 Z" fill="var(--teal)"/>
      <path d="M0,160 C120,135 260,160 380,235 C490,305 600,370 746,338" fill="none" stroke="var(--black)" stroke-width="1.5"/>
    </svg>

    <div class="wordmark">
      <div class="wordmark__row">
        <span class="wordmark__name">Ridgeworth Rentals LLC</span>
        <span class="wordmark__dot"></span>
      </div>
      <span class="wordmark__motto">Providing clean, safe, and affordable housing</span>
    </div>

    <p class="holder-name">BRENT KOVALICH</p>

    <address class="address" style="font-style:normal">
      2140 Larkspur Court<br>Fairbanks, Alaska 34819
    </address>

    <ul class="contact-list">
      <li>
        <svg viewBox="0 0 24 24" aria-hidden="true"><path d="M6.6 10.8a15.2 15.2 0 0 0 6.6 6.6l2.2-2.2a1 1 0 0 1 1-.25 11.4 11.4 0 0 0 3.6.57 1 1 0 0 1 1 1V20a1 1 0 0 1-1 1A17 17 0 0 1 3 4a1 1 0 0 1 1-1h3.5a1 1 0 0 1 1 1c0 1.25.2 2.45.57 3.57a1 1 0 0 1-.25 1z"/></svg>
        480-555-3174
      </li>
      <li>
        <svg viewBox="0 0 24 24" aria-hidden="true"><path d="M2 5h20v14H2z M3.5 6.5 12 12.5l8.5-6" fill="var(--white)" stroke="var(--teal)" stroke-width="1.6"/></svg>
        brentkovalich@ridgeworthrentals.example
      </li>
      <li>
        <svg viewBox="0 0 24 24" aria-hidden="true"><circle cx="12" cy="12" r="10"/><path d="M2 12h20M12 2c3 3 3 17 0 20M12 2c-3 3-3 17 0 20" fill="none" stroke="var(--teal)" stroke-width="1.4"/></svg>
        www.ridgeworthrentals.example
      </li>
    </ul>
  </section>

  <section class="card card--back" aria-label="Card back">
    <div class="back-band"></div>
    <div class="wordmark">
      <div class="wordmark__row">
        <span class="wordmark__name">Ridgeworth Rentals LLC</span>
        <span class="wordmark__dot"></span>
      </div>
      <span class="wordmark__motto">Providing clean, safe, and affordable housing</span>
    </div>

    <div class="note-field field-met">MET/VISITED:<span class="note-field__line" style="width:260px"></span></div>
    <div class="note-field field-date">DATE:<span class="note-field__line" style="width:175px"></span></div>
    <div class="note-field field-interests">INTERETS:<span class="note-field__line" style="width:530px"></span></div>
    <div class="blank-line"></div>
  </section>

</div>
</body>
</html>
```